Communications Consultancy needs Print Design Project

We are a communications consultancy providing training and services for organisations and individuals.

We have developed a Project Communication Strategy Model that is sound in functionality but poor in graphical design and structure.

We need to create a single page document that is a practical and profession tool to guide Project Managers through the process of communicating project outcomes.

The model will be used as a hard copy resource and will also need to be replicated onto a PowerPoint slide for instructional purposes.

Target Market(s)

Project Management Professionals

Industry/Entity Type

Communications

Requirements
Must have
• Icons to represent the different communication mediums (icons shown in attachment are just for example)

Enable future editing and be transfereable to PowerPoint

Have the company Logo (this can be privided as vector file etc.

Company contact details, website, phone, ABN etc.

```html
<!DOCTYPE html>
<html lang="en">
<head>
<meta charset="utf-8">
<title>Project Communication Strategy Model</title>
<link rel="stylesheet" href="https://fonts.googleapis.com/css2?family=Montserrat:wght@600;700;800&family=Oswald:wght@400&display=swap">
<style>
:root{
  --frame:#4a4a4a;
  --panel:#ffffff;
  --lime:#8be02a;
  --ink:#1d1d1d;
  --mid:#555;
  --strip:#dde2e3;
  --orange:#f26a1b;
  --page:#eeeeee;
  --white:#ffffff;
}
*{box-sizing:border-box;margin:0;padding:0}
html,body{width:1200px;height:865px;overflow:hidden;background:var(--page)}
body{font-family:"Montserrat",Arial,sans-serif;position:relative}
.sheet{position:absolute;left:11px;top:17px;width:989px;height:698px;background:var(--frame);transform:scale(1.19);transform-origin:0 0}
.abs{position:absolute}
.title{left:21px;top:24px;color:var(--lime);font-weight:700;font-size:22px;letter-spacing:-.2px}
.brand{right:22px;top:28px;color:var(--white);font-weight:700;font-size:18px;letter-spacing:.2px;line-height:1;white-space:nowrap}
.panel{left:6px;top:73px;width:975px;height:587px;background:var(--panel);border-radius:14px}
.tile{border:3px solid var(--lime);border-radius:10px;background:linear-gradient(90deg,#fff 0%,#9a9a9a 50%,#222 100%);display:flex;align-items:center;justify-content:center;font-weight:700;color:var(--ink)}
.event{left:17px;top:78px;width:144px;height:122px;font-size:26px;font-weight:800}
.audience{width:122px;height:77px;font-size:12px}
.bar{border:2px solid var(--lime);border-radius:6px;background:linear-gradient(90deg,#fff 0%,#bbb 40%,#111 100%);display:flex;align-items:center;justify-content:center;font-weight:700;font-size:11.5px;color:var(--ink);height:22px}
.bar.wide{background:linear-gradient(90deg,#fff 0%,#ccc 25%,#888 55%,#111 100%)}
.wire{background:var(--lime)}
.arrow{left:70px;top:306px;width:0;height:0;border-left:9px solid transparent;border-right:9px solid transparent;border-top:14px solid var(--lime)}
.strip{left:305px;top:264px;width:280px;height:46px;background:var(--strip)}
.technique{top:302px;color:var(--lime);font-family:"Oswald",Arial,sans-serif;font-size:12px}
.priority{top:300px;width:10px;color:var(--lime);font-weight:700;font-size:8px;line-height:9px;text-align:center}
.slots{left:149px;width:145px;font-weight:600;font-size:10.5px;color:var(--mid);line-height:16.5px;white-space:pre;overflow:hidden}
.step{width:132px;height:36px;border:3px solid var(--lime);border-radius:8px;background:#fff;color:var(--lime);font-weight:700;font-size:19px;display:flex;align-items:center;justify-content:center;top:610px}
.footer{left:17px;top:670px;color:#fff;font-weight:700;font-size:12.2px;white-space:nowrap}
</style>
</head>
<body>
<main class="sheet">
  <h1 class="abs title">Project Communication Strategy Model</h1>
  <div class="abs brand">Northgate Communications</div>

  <section class="abs panel"></section>

  <div class="abs tile event">EVENT</div>
  <div class="abs wire" style="left:161px;top:139px;width:25px;height:3px"></div>
  <div class="abs wire" style="left:257px;top:112px;width:3px;height:56px"></div>
  <div class="abs wire" style="left:333px;top:100px;width:16px;height:3px"></div>
  <div class="abs wire" style="left:331px;top:177px;width:20px;height:3px"></div>
  <div class="abs wire" style="left:348px;top:177px;width:3px;height:49px"></div>
  <div class="abs wire" style="left:78px;top:223px;width:273px;height:3px"></div>
  <div class="abs wire" style="left:78px;top:223px;width:3px;height:19px"></div>
  <div class="abs wire" style="left:78px;top:263px;width:3px;height:44px"></div>
  <div class="abs arrow"></div>

  <div class="abs bar" style="left:185px;top:91px;width:148px">NO</div>
  <div class="abs bar" style="left:348px;top:91px;width:146px">END</div>
  <div class="abs bar" style="left:186px;top:129px;width:147px">REPORTABLE?</div>
  <div class="abs bar" style="left:185px;top:167px;width:146px">YES</div>

  <div class="abs bar wide" style="left:12px;top:241px;width:283px">CHANNEL</div>
  <div class="abs bar wide" style="left:305px;top:241px;width:283px">MEDIUM</div>
  <div class="abs bar wide" style="left:598px;top:241px;width:376px">DELIVERY</div>
  <div class="abs bar wide" style="left:599px;top:271px;width:270px;height:23px">INFLUENCING TECHNIQUE</div>
  <div class="abs bar" style="left:877px;top:271px;width:98px;height:23px">PRIORITY</div>

  <svg class="abs strip" viewBox="0 0 280 46" role="img" aria-label="Medium icons: email, phone, card, laptop, message, meeting">
    <g transform="translate(8,10)">
      <rect width="34" height="26" rx="3" fill="#7ed321"/>
      <path d="M2 3 L17 15 L32 3" fill="none" stroke="#fff" stroke-width="2.5"/>
    </g>
    <g transform="translate(58,6)">
      <rect width="18" height="33" rx="3" fill="#7ed321"/>
      <rect x="3" y="4" width="12" height="9" fill="#fff"/>
      <g fill="#fff"><rect x="3" y="16" width="3" height="3"/><rect x="7.5" y="16" width="3" height="3"/><rect x="12" y="16" width="3" height="3"/><rect x="3" y="21" width="3" height="3"/><rect x="7.5" y="21" width="3" height="3"/><rect x="12" y="21" width="3" height="3"/><rect x="3" y="26" width="3" height="3"/><rect x="7.5" y="26" width="3" height="3"/><rect x="12" y="26" width="3" height="3"/></g>
    </g>
    <g transform="translate(96,10)">
      <rect width="34" height="25" rx="4" fill="#3a3a3a"/>
      <rect x="3" y="3" width="28" height="19" rx="2" fill="#fff"/>
      <rect x="6" y="7" width="8" height="10" fill="#3a3a3a"/>
      <rect x="17" y="8" width="11" height="2" fill="#3a3a3a"/><rect x="17" y="12" width="11" height="2" fill="#3a3a3a"/>
    </g>
    <g transform="translate(148,8)">
      <rect x="3" width="30" height="22" rx="2" fill="var(--orange)"/>
      <rect x="6" y="3" width="24" height="16" fill="#fff"/>
      <rect y="23" width="36" height="5" rx="2" fill="var(--orange)"/>
    </g>
    <g transform="translate(200,6)">
      <rect width="26" height="18" rx="4" fill="var(--orange)"/>
      <path d="M6 18 L6 25 L13 18 Z" fill="var(--orange)"/>
      <rect x="5" y="5" width="16" height="2" fill="#fff"/><rect x="5" y="10" width="12" height="2" fill="#fff"/>
    </g>
    <g transform="translate(238,8)">
      <rect width="32" height="30" rx="5" fill="#b9bfc1"/>
    </g>
  </svg>

  <span class="abs technique" style="left:599px">Rational</span>
  <span class="abs technique" style="left:658px">Emotional</span>
  <span class="abs technique" style="left:726px">Consultation</span>
  <span class="abs technique" style="left:804px">Collaboration</span>

  <div class="abs priority" style="left:885px">H<br>I<br>G<br>H</div>
  <div class="abs priority" style="left:923px">M<br>E<br>D<br>I<br>U<br>M</div>
  <div class="abs priority" style="left:955px">L<br>O<br>W</div>

  <div class="abs tile audience" style="left:17px;top:328px">Management</div>
  <div class="abs tile audience" style="left:18px;top:425px">Stakeholders</div>
  <div class="abs tile audience" style="left:18px;top:520px">Project Team</div>

  <div class="abs slots" style="top:326px">1....................................................
2....................................................
3....................................................
4....................................................
5....................................................</div>
  <div class="abs slots" style="top:415px">1....................................................
2....................................................
3....................................................
4....................................................
5....................................................</div>
  <div class="abs slots" style="top:513px">1....................................................
2....................................................
3....................................................
4....................................................
5....................................................</div>

  <div class="abs step" style="left:49px">Who</div>
  <div class="abs step" style="left:295px;width:130px">What</div>
  <div class="abs step" style="left:543px;width:130px">How</div>
  <div class="abs step" style="left:799px;width:131px">When</div>

  <p class="abs footer">Northgate Communications Pty.Ltd/ www.northgatecommunications.com.au / PO Box, Baywater NSW 2000/ +61 290001234 / ABN: 12 345 678 901</p>
</main>
</body>
</html>
```